Business Cards - Brightpath Horizon

need to design unique business card for my mortgage business. I need to design credit card style business card for my business or any unique idea that you might have

Target Market(s)

Home Loan customers

Industry/Entity Type

Mortgage Brokerage

Contact Information for Business Card

please design credit card style or very unique style business card

Colors

Designer to choose colors to be used in the design.

Requirements
Must have
• Name
• position
• Phone number
• fax number
• email address
• website address
• social media address
• All above fields will be provided once design in finalised

```html
<!DOCTYPE html>
<html lang="en">
<head>
<meta charset="utf-8">
<title>Brightpath Horizon – Business Card</title>
<link rel="stylesheet" href="https://fonts.googleapis.com/css2?family=Source+Sans+3:wght@400;600;700&display=swap">
<style>
  :root {
    --stage: #000000;
    --card-light: #f3f3f3;
    --brand-orange: #f7901e;
    --brand-orange-deep: #ec7f12;
    --brand-blue: #1b2fb0;
    --sky: #2aa6e0;
    --ink: #1e1e1e;
    --white: #ffffff;
  }
  * { margin: 0; padding: 0; box-sizing: border-box; }
  html, body { width: 1200px; height: 900px; overflow: hidden; background: var(--stage); }
  .stage { position: relative; width: 1200px; height: 900px; font-family: "Source Sans 3", "Myriad Pro", sans-serif; }

  .card { position: absolute; top: 200px; width: 310px; height: 502px; overflow: hidden; }
  .card-front { left: 265px; background: var(--card-light); border-radius: 62px 0 62px 0; }
  .card-back { left: 641px; width: 309px; background: var(--brand-orange); border-radius: 0 62px 0 62px; }

  .brand { position: absolute; left: 0; right: 0; display: flex; align-items: center; justify-content: center; gap: 10px; }
  .brand-name { font-weight: 700; font-size: 31px; line-height: 1.05; letter-spacing: 0.5px; }
  .brand-dot { width: 22px; height: 22px; border-radius: 50%; flex: none; }

  .card-front .brand { top: 87px; }
  .card-front .brand-name { color: var(--brand-blue); }
  .card-front .brand-dot { background: var(--sky); }

  .person { position: absolute; left: 25px; top: 326px; }
  .person-name { color: var(--brand-orange); font-weight: 700; font-size: 19px; line-height: 24px; }
  .person-role { color: var(--ink); font-size: 14px; line-height: 18px; }

  .contacts { position: absolute; left: 25px; top: 394px; list-style: none; }
  .contacts li { display: flex; align-items: center; gap: 8px; height: 20.7px; color: var(--ink); font-size: 14.5px; }
  .contacts svg { width: 10px; height: 10px; fill: var(--brand-orange); flex: none; }

  .backdrop { position: absolute; inset: 0; background: radial-gradient(ellipse at 70% 35%, var(--brand-orange-deep) 0%, rgba(236,127,18,0.35) 45%, rgba(247,144,30,0) 75%), linear-gradient(160deg, rgba(236,127,18,0) 35%, rgba(236,127,18,0.8) 75%); }
  .card-back .brand { top: 307px; }
  .card-back .brand-name { color: var(--white); }
  .card-back .brand-dot { background: var(--white); }
  .social { position: absolute; top: 428px; left: 0; right: 0; display: flex; justify-content: center; gap: 9px; }
  .social span { width: 30px; height: 30px; border-radius: 50%; background: var(--white); }
</style>
</head>
<body>
<main class="stage">
  <section class="card card-front">
    <div class="brand">
      <span class="brand-dot"></span>
      <div class="brand-name">Brightpath<br>Horizon</div>
    </div>

    <div class="person">
      <p class="person-name">Daniel Reeves</p>
      <p class="person-role">Managing Director</p>
    </div>

    <ul class="contacts">
      <li><svg viewBox="0 0 10 10"><path d="M2 0.5 L3.6 2.6 L2.7 3.7 Q3.8 5.9 6.3 7.3 L7.4 6.4 L9.5 8 L8.3 9.5 Q4.2 9 1.2 5.5 Q0.3 3.5 0.5 1.7 Z"/></svg>(055)-218-3406</li>
      <li><svg viewBox="0 0 10 10"><rect x="0.5" y="3" width="9" height="6.5" rx="1"/><rect x="2.5" y="0.5" width="5" height="3" fill="none" stroke="#f7901e"/></svg>321-654-0987</li>
      <li><svg viewBox="0 0 10 10"><rect x="0.5" y="2" width="9" height="6.5"/><path d="M0.5 2 L5 5.5 L9.5 2" stroke="#f3f3f3" fill="none"/></svg>info@brightpath.com</li>
      <li><svg viewBox="0 0 10 10"><circle cx="5" cy="5" r="4.5"/></svg>www.brightpath.com</li>
    </ul>
  </section>

  <section class="card card-back">
    <div class="backdrop" role="img" aria-label="Faint tone-on-tone rooftops and tree decoration"></div>
    <div class="brand">
      <span class="brand-dot"></span>
      <div class="brand-name">Brightpath<br>Horizon</div>
    </div>
    <div class="social" role="img" aria-label="Social media links">
      <span></span><span></span><span></span>
    </div>
  </section>
</main>
</body>
</html>
```